Simple Logo Design for Semi-Clear Plastic Frosted Card stock

Create a business card on frosted plastic. compliment existing logo elements with a tree trunk, roots, or seed at the lower half and the full logo both on the front.

Contact information will go on a solid portion of the back of this design since this card stock is semi-transparent.

It is important to consider this plastic card stock medium in your design. I found helpful tips and guides listed at vellaprint-sample.net: be careful to understand ink printed on plastic cards cannot have too much of a consistent print area or risks peeling and fine lines can easily scratch off.
Updates

2" x 3.5" 20PT Clear Plastic Business cards with Round corners Please get info or templates here: https://www.vellaprint-sample.net/product-detail/2-x-35-20pt-clear-plastic-business-cards-with-round-corners

Target Market(s)

Not for profit- religion

Industry/Entity Type

Business

Must include complementary elements to the existing logo

Font styles to use
Decorative

Colors
000000

Requirements
Must have
• Elements of community, nature and oneness. Such as: seed, roots, tree trunk, etc.
• Three lines of space on the back for Name, Title, Phone Number.
Nice to have
• I like a light use of decorative elements
Should not have
• No eyes, from faces or animals.

```html
<!DOCTYPE html>
<html lang="en">
<head>
<meta charset="utf-8">
<title>Havenroot Business Card</title>
<link href="https://fonts.googleapis.com/css2?family=Federo&family=Cinzel:wght@400;700&display=swap" rel="stylesheet">
<style>
  :root {
    --page-bg: #e6ebef;
    --frost: rgba(255, 255, 255, 0.62);
    --frost-edge: rgba(255, 255, 255, 0.9);
    --ink-green: #2f6b45;
    --ink-dark: #2b3236;
    --ink-muted: #4a5358;
    --rule: #56606a;
  }
  * { margin: 0; padding: 0; box-sizing: border-box; }
  html, body { width: 800px; height: 1200px; overflow: hidden; }
  body {
    background: var(--page-bg);
    display: flex;
    flex-direction: column;
    align-items: center;
    justify-content: center;
    gap: 150px;
  }
  .card {
    position: relative;
    width: 600px;
    height: 343px;
    border-radius: 18px;
    background: var(--frost);
    border: 1px solid var(--frost-edge);
    box-shadow: 0 6px 24px rgba(60, 75, 90, 0.12);
    overflow: hidden;
  }
  .brand {
    position: absolute;
    display: flex;
    flex-direction: column;
  }
  .brand-row { display: flex; align-items: center; gap: 12px; }
  .brand-dot { border-radius: 50%; background: var(--ink-green); flex: none; }
  .brand-name {
    font-family: "Federo", sans-serif;
    color: var(--ink-green);
    letter-spacing: 0.02em;
    line-height: 1;
  }
  .brand-tagline {
    font-family: "Cinzel", serif;
    color: var(--ink-dark);
    letter-spacing: 0.06em;
    text-transform: uppercase;
  }

  /* back */
  .card--back .brand { top: 118px; left: 24px; align-items: center; }
  .card--back .brand-dot { width: 20px; height: 20px; }
  .card--back .brand-name { font-size: 38px; }
  .card--back .brand-tagline { font-size: 10px; margin-top: 6px; }
  .contact-name {
    position: absolute;
    left: 24px; top: 230px;
    font-family: "Cinzel", serif;
    font-weight: 700;
    font-size: 20px;
    line-height: 24px;
    color: var(--ink-dark);
  }
  .contact-title {
    position: absolute;
    left: 24px; top: 255px;
    font-family: "Cinzel", serif;
    font-size: 10px;
    line-height: 12px;
    color: var(--ink-muted);
    letter-spacing: 0.05em;
  }
  .contact-rule {
    position: absolute;
    left: 24px; right: 0;
    top: 268px;
    height: 1.5px;
    background: var(--rule);
  }
  .contact-lines {
    position: absolute;
    left: 24px; top: 276px;
    font-family: "Cinzel", serif;
    font-size: 12px;
    color: var(--ink-dark);
    line-height: 20px;
  }
  .contact-lines li { list-style: none; display: flex; align-items: center; gap: 8px; }
  .contact-lines svg { width: 11px; height: 11px; fill: var(--ink-dark); }

  /* front */
  .card--front .brand { top: 176px; left: 0; right: 0; align-items: center; }
  .card--front .brand-dot { width: 30px; height: 30px; }
  .card--front .brand-name { font-size: 56px; }
  .card--front .brand-tagline { font-size: 14px; margin-top: 8px; }
</style>
</head>
<body>
  <section class="card card--back" aria-label="Card back with contact details">
    <div class="brand">
      <div class="brand-row">
        <span class="brand-dot"></span>
        <span class="brand-name">HAVENROOT</span>
      </div>
      <p class="brand-tagline">Learning, Fellowship &amp; Calm</p>
    </div>
    <p class="contact-name">LEON HARTWELL</p>
    <p class="contact-title">DIRECTOR</p>
    <div class="contact-rule"></div>
    <ul class="contact-lines">
      <li>
        <svg viewBox="0 0 24 24" aria-hidden="true"><path d="M6.6 10.8a15.1 15.1 0 0 0 6.6 6.6l2.2-2.2a1 1 0 0 1 1-.25 11.4 11.4 0 0 0 3.6.57 1 1 0 0 1 1 1V20a1 1 0 0 1-1 1A17 17 0 0 1 3 4a1 1 0 0 1 1-1h3.5a1 1 0 0 1 1 1c0 1.25.2 2.45.57 3.570a1 1 0 0 1-.25 1z"/></svg>
        +330 2815-4092
      </li>
      <li>
        <svg viewBox="0 0 24 24" aria-hidden="true"><path d="M2 5h20v14H2zm2 2v.5l8 5 8-5V7zm0 2.8V17h16V9.8l-8 5z"/></svg>
        LEONHARTWELL@HAVENMAIL.ORG
      </li>
    </ul>
  </section>

  <section class="card card--front" aria-label="Card front with brand name">
    <div class="brand">
      <div class="brand-row">
        <span class="brand-dot"></span>
        <span class="brand-name">HAVENROOT</span>
      </div>
      <p class="brand-tagline">Learning, Fellowship &amp; Calm</p>
    </div>
  </section>
</body>
</html>
```